We have a company that provide sandblasted stone products. Example: numbers for houses. Also we sell cultured stone,brick natural stone to the contractor,homeowner. We need to get a business card that describe our product and service. In the original idea we had an old fashion chisel striking through the x in velquarin.

Reason: We realized that 2 days was not enough time for the competion to be open many of the designers may be to busy and require more time to compete.

Industry/Entity Type

It Company

Logo Text

Velquarin

```html
<!DOCTYPE html>
<html lang="en">
<head>
<meta charset="utf-8">
<title>Velquarin Business Card</title>
<link href="https://fonts.googleapis.com/css2?family=Arimo:wght@400;700&display=swap" rel="stylesheet">
<style>
  :root {
    --backdrop: #e9e7e4;
    --card: #ffffff;
    --card-front: #f7f7f7;
    --teal: #6fa3b1;
    --ink: #2b2b2b;
    --ink-soft: #4a4a4a;
    --brand-ink: #4d4d4d;
    --shadow: rgba(0, 0, 0, 0.16);
  }
  * { box-sizing: border-box; margin: 0; padding: 0; }
  html, body {
    width: 1200px;
    height: 900px;
    overflow: hidden;
    background: var(--backdrop);
    font-family: "Arimo", Arial, sans-serif;
  }
  .stage {
    width: 1200px;
    height: 900px;
    display: flex;
    flex-direction: column;
    align-items: center;
    justify-content: center;
    gap: 60px;
  }
  .card {
    width: 560px;
    height: 320px;
    box-shadow: 0 6px 18px var(--shadow);
    position: relative;
    overflow: hidden;
  }
  .card-back {
    background: var(--card);
    display: flex;
  }
  .card-back .contact {
    flex: 1;
    padding: 34px 0 0 38px;
    color: var(--ink);
    line-height: 1.2;
  }
  .contact .name {
    font-weight: 700;
    font-size: 20px;
  }
  .contact .role {
    font-size: 14px;
    color: var(--ink-soft);
    margin-bottom: 10px;
  }
  .contact .details {
    font-size: 14px;
    color: var(--ink-soft);
    list-style: none;
    line-height: 1.3;
  }
  .card-back .accent-band {
    width: 96px;
    background: var(--teal);
  }
  .card-front {
    background: var(--card-front);
    display: flex;
    align-items: center;
    justify-content: center;
    gap: 14px;
  }
  .brand-dot {
    width: 22px;
    height: 22px;
    border-radius: 50%;
    background: var(--teal);
  }
  .brand-name {
    font-size: 36px;
    font-weight: 400;
    letter-spacing: 1px;
    color: var(--brand-ink);
  }
</style>
</head>
<body>
  <main class="stage">
    <section class="card card-back" aria-label="Business card, contact side">
      <div class="contact">
        <p class="name">Marta Kellin</p>
        <p class="role">Chief Executive Officer</p>
        <ul class="details">
          <li>Unit 12</li>
          <li>48 Ridgeway Road, Canada</li>
          <li>Tel: 2871 904</li>
          <li>Mob: 2871 935</li>
          <li>Email: marta@velquarin.com</li>
          <li>www.velquarin.com</li>
        </ul>
      </div>
      <div class="accent-band"></div>
    </section>

    <section class="card card-front" aria-label="Business card, brand side">
      <span class="brand-dot"></span>
      <span class="brand-name">VELQUARIN</span>
    </section>
  </main>
</body>
</html>
```